Redesign of business card for Cedar Ridge Mechanical

We are looking for a new design for our business cards for Cedar Ridge Mechanical. We are a plumbing & HVAC construction company, operating on the West Coast of Canada and USA. Logo attached.
Industry/Entity Type
Construction - Plumbing & HVAC
Contact Information for Business Card
Name, address, phone numbers, email, website address
Look and feel
Each slider illustrates characteristics of the customer's brand and the style your logo design should communicate.

```html
<!DOCTYPE html>
<html lang="en">
<head>
<meta charset="utf-8">
<title>Cedar Ridge Mechanical – Business Card</title>
<link href="https://fonts.googleapis.com/css2?family=Poppins:wght@300;400;500;600;700&display=swap" rel="stylesheet">
<style>
  :root {
    --stage: #d9d6d0;
    --frame: #0d0d0d;
    --paper: #e6e7e8;
    --ink: #111111;
    --emboss: #cfd0d2;
    --notch: #ffffff;
  }
  * { margin: 0; padding: 0; box-sizing: border-box; }
  html, body { width: 1200px; height: 711px; overflow: hidden; }
  body {
    background: var(--stage);
    font-family: "Poppins", sans-serif;
    color: var(--ink);
    position: relative;
  }
  .card {
    position: absolute;
    top: 200px;
    width: 540px;
    height: 310px;
    background: var(--frame);
    border-radius: 22px;
  }
  .card--front { left: 30px; }
  .card--back { left: 630px; }
  .card__panel {
    position: absolute;
    inset: 14px;
    background: var(--paper);
    border-radius: 12px;
    overflow: hidden;
  }
  .card__notch {
    position: absolute;
    width: 3px;
    height: 14px;
    background: var(--notch);
  }
  .card__notch--tl { top: 0; left: 34px; }
  .card__notch--tr { top: 0; right: 34px; }
  .card__notch--bl { bottom: 0; left: 34px; }
  .card__notch--br { bottom: 0; right: 34px; }

  /* Front */
  .front__brand {
    position: absolute;
    inset: 0;
    display: flex;
    align-items: center;
    justify-content: center;
    gap: 16px;
  }
  .front__mark {
    width: 44px; height: 44px;
    border: 5px solid var(--emboss);
  }
  .front__name {
    font-weight: 600;
    font-size: 30px;
    letter-spacing: 1px;
    text-transform: uppercase;
    color: var(--emboss);
    line-height: 1.1;
  }

  /* Back */
  .back__brand {
    position: absolute;
    left: 28px; top: 96px;
    width: 200px;
    display: flex;
    align-items: center;
    gap: 12px;
  }
  .back__mark {
    flex: none;
    width: 34px; height: 34px;
    border: 5px solid var(--ink);
  }
  .back__name {
    font-weight: 700;
    font-size: 19px;
    line-height: 1.15;
    text-transform: uppercase;
  }
  .back__divider {
    position: absolute;
    left: 244px; top: 56px;
    width: 1px; height: 150px;
    background: var(--ink);
  }
  .back__person {
    position: absolute;
    left: 268px; top: 50px;
  }
  .person__name { font-size: 27px; line-height: 1.1; }
  .person__first { font-weight: 700; }
  .person__last { font-weight: 300; }
  .person__title { font-weight: 600; font-size: 11.5px; margin-top: 2px; }
  .contact {
    position: absolute;
    left: 276px; top: 132px;
    list-style: none;
    font-size: 12.5px;
    line-height: 22px;
  }
  .contact__item { display: flex; align-items: center; gap: 9px; }
  .contact__icon { width: 12px; height: 12px; flex: none; }
  .back__address {
    position: absolute;
    left: 0; right: 0; bottom: 22px;
    text-align: center;
    font-size: 12.5px;
  }
</style>
</head>
<body>

<section class="card card--front" aria-label="Card front">
  <span class="card__notch card__notch--tl"></span>
  <span class="card__notch card__notch--tr"></span>
  <span class="card__notch card__notch--bl"></span>
  <span class="card__notch card__notch--br"></span>
  <div class="card__panel">
    <div class="front__brand">
      <span class="front__mark"></span>
      <span class="front__name">Cedar Ridge<br>Mechanical</span>
    </div>
  </div>
</section>

<section class="card card--back" aria-label="Card back">
  <span class="card__notch card__notch--tl"></span>
  <span class="card__notch card__notch--tr"></span>
  <span class="card__notch card__notch--bl"></span>
  <span class="card__notch card__notch--br"></span>
  <div class="card__panel">
    <div class="back__brand">
      <span class="back__mark"></span>
      <span class="back__name">Cedar Ridge<br>Mechanical</span>
    </div>
    <div class="back__divider"></div>
    <div class="back__person">
      <p class="person__name"><span class="person__first">Marta</span> <span class="person__last">Kovalova</span></p>
      <p class="person__title">Founder &amp; CEO</p>
    </div>
    <ul class="contact">
      <li class="contact__item">
        <svg class="contact__icon" viewBox="0 0 24 24"><path fill="currentColor" d="M6.6 10.8a15.1 15.1 0 0 0 6.6 6.6l2.2-2.2c.3-.3.7-.4 1-.2 1.1.4 2.3.6 3.6.6.6 0 1 .4 1 1V20c0 .6-.4 1-1 1C10.6 21 3 13.4 3 4c0-.6.4-1 1-1h3.5c.6 0 1 .4 1 1 0 1.3.2 2.5.6 3.6.1.3 0 .7-.2 1z"/></svg>
        (604) 555-0148
      </li>
      <li class="contact__item">
        <svg class="contact__icon" viewBox="0 0 24 24"><rect x="2" y="5" width="20" height="14" rx="2" fill="none" stroke="currentColor" stroke-width="2.4"/><path d="M3 6l9 7 9-7" fill="none" stroke="currentColor" stroke-width="2.4"/></svg>
        info@yourwebsite.com
      </li>
      <li class="contact__item">
        <svg class="contact__icon" viewBox="0 0 24 24"><circle cx="12" cy="12" r="10" fill="none" stroke="currentColor" stroke-width="2.4"/><path d="M2 12h20M12 2c3 3 3 17 0 20M12 2c-3 3-3 17 0 20" fill="none" stroke="currentColor" stroke-width="2"/></svg>
        www.yourwebsite.com
      </li>
    </ul>
    <p class="back__address">1840 Harbor View Rd. Suite 300 Vancouver, BC V6B 2K9</p>
  </div>
</section>

</body>
</html>
```